Wine label for premium wine of vinery Mirelovac.

Design Premium wine label.

The brand is called Telvora. Brand can be extended to Ambero Telvora. There
The label should be unique and high class feeling.
This is facebook lonk of the winery
https://www.sociloop.net/402918375510264/

On facebook you can see some examole of labels that are used now. Winery is called Mirelovac, so they used letter "M" as a logo in different ways
Updates

Need extra days to review

Target Market(s)

Premium high class yet modern living traditional but also gadget fun.
I have uploaded few inspirational photos that the owner of the vinery likes. Hope it helps.

Industry/Entity Type

Vinery

Requirements
Must have
• Black, gold, silver color to be dominated. Colors that are NOT acceptable are: green, yellow, blue, purple, pink.

The name of the vinary is Mirelovac and it should be on the front label.
Nice to have
• The size of label should fit the Sorbelo application screenshot frame.
Should not have
• Cheap perception of the label and brand

```html
<!DOCTYPE html>
<html lang="en">
<head>
<meta charset="utf-8">
<title>Mirelovac – Ambero Telvora Cabernet Sauvignon label</title>
<link rel="stylesheet" href="https://fonts.googleapis.com/css2?family=Josefin+Sans:wght@300;400&family=Playfair+Display:wght@400&family=Oswald:wght@400&display=swap">
<style>
  :root {
    --page-bg: #ffffff;
    --label-black: #141414;
    --label-black-soft: #1c1c1c;
    --gold-light: #e8b84a;
    --gold: #d3a23c;
    --gold-deep: #a9782a;
    --silver-text: #e9e9e9;
    --band-ink: #2a2012;
    --engraving-dark: #1a1a1a;
    --engraving-mid: #3a3a3a;
  }
  * { box-sizing: border-box; margin: 0; padding: 0; }
  html, body {
    width: 1200px;
    height: 992px;
    overflow: hidden;
    background: var(--page-bg);
  }
  .canvas {
    position: relative;
    width: 1200px;
    height: 992px;
  }
  .wine-label {
    position: absolute;
    left: 270px;
    top: 46px;
    width: 660px;
    height: 900px;
    background: linear-gradient(180deg, var(--label-black-soft) 0%, var(--label-black) 100%);
    overflow: hidden;
  }
  .winery-name {
    position: absolute;
    top: 148px;
    left: 0;
    width: 100%;
    text-align: center;
    font-family: "Josefin Sans", sans-serif;
    font-weight: 300;
    font-size: 104px;
    line-height: 1;
    letter-spacing: 2px;
    color: var(--gold);
  }
  .wine-origin {
    position: absolute;
    top: 374px;
    left: 0;
    width: 100%;
    text-align: center;
    font-family: "Josefin Sans", sans-serif;
    font-weight: 300;
    font-size: 25px;
    letter-spacing: 4px;
    color: var(--silver-text);
  }
  .wine-variety {
    position: absolute;
    top: 406px;
    left: 0;
    width: 100%;
    text-align: center;
    font-family: "Josefin Sans", sans-serif;
    font-weight: 300;
    font-size: 25px;
    letter-spacing: 4px;
    color: var(--gold);
  }
  .vintage-box {
    position: absolute;
    top: 460px;
    left: 296px;
    width: 68px;
    height: 65px;
    border: 1px solid var(--silver-text);
    display: flex;
    flex-direction: column;
    align-items: center;
    justify-content: center;
    font-family: "Playfair Display", serif;
    font-size: 22px;
    line-height: 1.05;
    color: var(--silver-text);
  }
  .vineyard-scene {
    position: absolute;
    left: 0;
    top: 528px;
    width: 100%;
    height: 260px;
    background:
      radial-gradient(ellipse 70% 60% at 50% 100%, var(--engraving-mid) 0%, var(--engraving-dark) 70%, transparent 100%),
      linear-gradient(180deg, var(--label-black) 0%, var(--engraving-dark) 100%);
  }
  .info-band {
    position: absolute;
    left: 0;
    bottom: 0;
    width: 100%;
    height: 112px;
    background: linear-gradient(90deg, var(--gold-deep) 0%, var(--gold-light) 30%, var(--gold) 65%, var(--gold-deep) 100%);
    display: flex;
    align-items: center;
    justify-content: center;
  }
  .volume-alcohol {
    font-family: "Oswald", sans-serif;
    font-size: 25px;
    letter-spacing: 6px;
    color: var(--band-ink);
  }
</style>
</head>
<body>
  <main class="canvas">
    <section class="wine-label">
      <h1 class="winery-name">Mirelovac</h1>
      <p class="wine-origin">AMBERO TELVORA</p>
      <p class="wine-variety">CABERNET SAUVIGNON</p>
      <div class="vintage-box"><span>20</span><span>18</span></div>
      <div class="vineyard-scene" role="img" aria-label="Engraved landscape of rolling vineyard hills with a village and cypress trees"></div>
      <footer class="info-band">
        <span class="volume-alcohol">750ML. | 13.5% ALC/VOL</span>
      </footer>
    </section>
  </main>
</body>
</html>
```